Business card design for holistic health care clinic

We need a double-sided business card design for our holistic health care clinic that integrates our logo design and also its color scheme. My business is called Valmira. It is an integrative medicine clinic. You have already done the logo for me. Please ensure an elegant and upscale design that is not cluttered, but still has all the necessary information (please see below for details).

Target Market(s)

Wellness, fitness, rehabilitation for educated, well-traveled open-minded clients who are focused on natural, organic, balanced and preventive healthcare and lifestyle.

Industry/Entity Type

Medical

Contact Information for Business Card

Modern, clean.

Number of Pages Required

1 page

Font styles to use
Serif
Sans Serif

Colors

Designer to choose colors to be used in the design.

Requirements
Must have
• Logo on one side, all other information on the other side.
• Other information should include:
• Tobias Wrenfeld - DOE, CPT, LMT
• 4100 East Marrow Drive
• Austin, TX 78119
• 512 555 0148
• 818 555 0192
• info@ValmiraHealth.example
• t.wrenfeld@ValmiraHealth.example
Nice to have
• Darker background on front - but not totally black - shaded/dark gray.

```html
<!DOCTYPE html>
<html lang="en">
<head>
<meta charset="utf-8">
<title>Valmira – Business Card</title>
<link href="https://fonts.googleapis.com/css2?family=Roboto+Condensed:wght@700&family=Source+Sans+3:ital,wght@0,400;0,700;1,600&display=swap" rel="stylesheet">
<style>
  :root {
    --page: #e2e2e2;
    --brand-blue: #0a86c0;
    --card-dark: #2a2a2a;
    --card-dark-deep: #232323;
    --ink-light: #ffffff;
  }
  * { margin: 0; padding: 0; box-sizing: border-box; }
  html, body { width: 1200px; height: 808px; overflow: hidden; }
  body {
    background: var(--page);
    font-family: "Source Sans 3", sans-serif;
    position: relative;
  }
  .card {
    position: absolute;
    width: 505px;
    height: 289px;
    background: linear-gradient(180deg, var(--card-dark-deep), var(--card-dark));
    box-shadow: 1px 3px 5px rgba(0,0,0,0.35);
    overflow: hidden;
  }
  .card--info { left: 351px; top: 95px; }
  .card--brand { left: 349px; top: 398px; }

  .info-panel {
    position: absolute;
    left: 0; top: 0;
    width: 234px; height: 100%;
    background: var(--brand-blue);
    color: var(--ink-light);
    overflow: hidden;
  }
  .divider {
    position: absolute;
    left: 236px; top: 0;
    width: 4px; height: 100%;
    background: var(--brand-blue);
  }
  .holder {
    position: absolute;
    left: 20px; top: 86px;
    font-family: "Roboto Condensed", sans-serif;
    font-weight: 700;
    font-size: 16px;
    white-space: nowrap;
  }
  .holder .credentials { font-size: 10px; }
  .address {
    position: absolute;
    left: 20px; top: 114px;
    font-size: 12.5px;
    line-height: 16px;
  }
  .contacts {
    position: absolute;
    left: 20px; top: 153px;
    list-style: none;
    font-size: 11px;
    line-height: 15px;
  }
  .contacts li { display: flex; align-items: center; white-space: nowrap; }
  .contacts svg { width: 10px; height: 10px; margin-right: 6px; flex: none; }

  .brand {
    position: absolute;
    text-align: center;
    color: var(--brand-blue);
  }
  .brand-name {
    font-weight: 700;
    line-height: 1;
    display: block;
  }
  .brand-line {
    font-weight: 700;
    display: block;
    margin-top: 4px;
  }
  .card--info .brand { left: 250px; width: 245px; top: 126px; }
  .card--info .brand-name { font-size: 46px; }
  .card--info .brand-line { font-size: 13px; }
  .card--brand .brand { left: 0; width: 100%; top: 118px; }
  .card--brand .brand-name { font-size: 52px; }
  .card--brand .brand-line { font-size: 15px; }

  .slogan {
    position: absolute;
    left: 0; width: 100%;
    top: 232px;
    text-align: center;
    color: var(--ink-light);
    font-style: italic;
    font-weight: 600;
    font-size: 13px;
  }
</style>
</head>
<body>
  <section class="card card--info" aria-label="Contact side">
    <div class="info-panel">
      <p class="holder">TOBIAS WRENFELD <span class="credentials">- DOE, CPT, LMT</span></p>
      <p class="address">4100 East Marrow Drive<br>Austin, TX 78119</p>
      <ul class="contacts">
        <li><svg viewBox="0 0 12 12" aria-hidden="true"><path fill="#fff" d="M1 4c0-2 2-3 5-3s5 1 5 3l-2 1-1-1.5H4L3 5zM3 6h6l1 5H2z"/></svg>512 555 0148</li>
        <li><svg viewBox="0 0 12 12" aria-hidden="true"><rect x="3" y="0.5" width="6" height="11" rx="1" fill="#fff"/><rect x="4" y="2" width="4" height="6.5" fill="#0a86c0"/></svg>818 555 0192</li>
        <li><svg viewBox="0 0 12 12" aria-hidden="true"><rect x="0.5" y="2.5" width="11" height="7" fill="#fff"/><path d="M1 3l5 3.5L11 3" stroke="#0a86c0" fill="none"/></svg>t.wrenfeld@ValmiraHealth.example</li>
        <li><svg viewBox="0 0 12 12" aria-hidden="true"><rect x="0.5" y="2.5" width="11" height="7" fill="#fff"/><path d="M1 3l5 3.5L11 3" stroke="#0a86c0" fill="none"/></svg>info@ValmiraHealth.example</li>
        <li><svg viewBox="0 0 12 12" aria-hidden="true"><circle cx="6" cy="6" r="5.5" fill="#fff"/><path d="M3 4h3v3H4zM7 7h2v2H7z" fill="#0a86c0"/></svg>www.ValmiraHealth.example</li>
      </ul>
    </div>
    <div class="divider"></div>
    <div class="brand">
      <span class="brand-name">VALMIRA</span>
      <span class="brand-line">Integrative Holistic Medicine</span>
    </div>
  </section>

  <section class="card card--brand" aria-label="Brand side">
    <div class="brand">
      <span class="brand-name">VALMIRA</span>
      <span class="brand-line">Integrative Holistic Medicine</span>
    </div>
    <p class="slogan">it’s all about you – your health, your objectives</p>
  </section>
</body>
</html>
```